Venture 482 - Lumora Book Cover

I am looking for a Lumora book cover for my book about "Venture 482".
The Book is Titled:
Venture 482 Ascended
Shaping Outcomes: Paths To Unlocking Cosmic Truths
Author is Dorian Pell
Here is a book description that may help you understand more about it:
Inspired by the genius of Edwin Marlowe, this comprehensive guide delves into the ancient wisdom and cutting-edge science behind the 482 method, a powerful tool for manifesting your desires. Whether you're seeking personal growth, financial success, or spiritual enlightenment, this book provides advanced techniques and methods to transform your dreams into reality.
Any questions please ask.
Thanks
Owen

```html
<!DOCTYPE html>
<html lang="en">
<head>
<meta charset="utf-8">
<title>Venture 482 Ascended — Book Cover</title>
<link href="https://fonts.googleapis.com/css2?family=Cormorant+Garamond:wght@400;500&family=Cinzel:wght@400&family=Tinos&display=swap" rel="stylesheet">
<style>
  :root {
    --page-bg: #e4e4e2;
    --cover-navy: #0b1220;
    --cover-deep: #1a1a2a;
    --glow-gold: #f2b23a;
    --glow-amber: #b4641c;
    --haze-blue: #2a3d63;
    --cream: #fbe8da;
    --shadow: rgba(0, 0, 0, 0.55);
  }
  html, body {
    margin: 0;
    width: 1200px;
    height: 1131px;
    overflow: hidden;
    background: var(--page-bg);
  }
  .book-cover {
    position: absolute;
    left: 240px;
    top: 18px;
    width: 720px;
    height: 1095px;
    overflow: hidden;
    background: var(--cover-navy);
    border-radius: 10px;
  }
  .cover-art {
    position: absolute;
    inset: 0;
    background:
      radial-gradient(ellipse 22% 40% at 50% 52%, rgba(242, 178, 58, 0.75), transparent 70%),
      radial-gradient(ellipse 30% 18% at 45% 14%, rgba(242, 178, 58, 0.55), transparent 70%),
      radial-gradient(ellipse 35% 30% at 88% 82%, rgba(242, 178, 58, 0.6), transparent 70%),
      radial-gradient(ellipse 30% 22% at 12% 60%, rgba(180, 100, 28, 0.55), transparent 70%),
      radial-gradient(ellipse 40% 30% at 80% 30%, rgba(42, 61, 99, 0.7), transparent 70%),
      radial-gradient(ellipse 40% 30% at 20% 30%, rgba(42, 61, 99, 0.6), transparent 70%),
      linear-gradient(180deg, var(--cover-deep), var(--cover-navy) 60%, #120d10);
  }
  .author,
  .title-word,
  .title-digit,
  .edition,
  .subtitle-lead,
  .subtitle-line {
    position: absolute;
    margin: 0;
    color: var(--cream);
    text-align: center;
  }
  .author {
    left: 0; right: 0;
    top: 62px;
    font-family: "Cinzel", "Cormorant Garamond", serif;
    font-size: 44px;
    letter-spacing: 0.28em;
    padding-left: 0.28em;
  }
  .title-word {
    left: 0; right: 0;
    top: 316px;
    font-family: "Cinzel", serif;
    font-size: 108px;
    line-height: 1;
    text-shadow: 0 2px 8px var(--shadow);
  }
  .title-digit {
    font-family: "Cormorant Garamond", serif;
    font-weight: 500;
    font-size: 300px;
    line-height: 1;
    text-shadow: 0 3px 10px var(--shadow);
  }
  .digit-one   { left: 175px; top: 430px; }
  .digit-two   { left: 300px; top: 500px; }
  .digit-three { left: 425px; top: 430px; }
  .edition {
    left: 0; right: 0;
    top: 788px;
    font-family: "Cinzel", serif;
    font-size: 58px;
    letter-spacing: 0.38em;
    padding-left: 0.38em;
    text-shadow: 0 2px 6px var(--shadow);
  }
  .subtitle-lead {
    left: 0; right: 0;
    top: 888px;
    font-family: "Tinos", "Times New Roman", serif;
    font-size: 25px;
    text-shadow: 0 1px 4px var(--shadow);
  }
  .subtitle-line {
    left: 0; right: 0;
    font-family: "Tinos", "Times New Roman", serif;
    font-size: 23px;
    line-height: 1;
    text-shadow: 0 1px 4px var(--shadow);
  }
  .subtitle-line.first  { top: 940px; }
  .subtitle-line.second { top: 973px; }
</style>
</head>
<body>
  <main class="book-cover">
    <div class="cover-art" role="img" aria-label="Illustration of a glowing golden human figure made of light and energy strands, surrounded by swirling gold and blue cosmic particles"></div>
    <p class="author">DORIAN PELL</p>
    <h1 class="title">
      <span class="title-word">Venture</span>
      <span class="title-digit digit-one">4</span>
      <span class="title-digit digit-two">8</span>
      <span class="title-digit digit-three">2</span>
    </h1>
    <p class="edition">ASCENDED</p>
    <p class="subtitle-lead">SHAPING OUTCOMES:</p>
    <p class="subtitle-line first">Paths to unlocking</p>
    <p class="subtitle-line second">cosmic truths</p>
  </main>
</body>
</html>
```